African homeware retailer needs a web page design

We need a web page design for a new homeware and accessories store based in Johannesburg, South Africa. Our store carries modern African inspired items from designers that support social development and poverty alleviation initiatives. We have a particular preference for outfits that are centred on the empowerment of women.

Our business celebrates the skill, design and product of African craft and the work of designers looking to take that forward in a socially beneficial way (creating employment, developing skills, supporting local crafts people etc). We aim to carry items and inspirations from all over the African continent.

We would like to see a design that communicates African beauty and elegance without the typical tribal references that are made in reference to African craft or art.

We would like the web page to be stylish, uncomplicated, modern, captivating and appealing to the discerning customer. A similar value proposition is that of http://www.marlowtenwick.example/.

This is an e-commerce website which must be attractive to both individual buyers and design professionals so the website needs to look professional.

Here are links to some websites we like:
http://www.quenbyhollis.example/
http://www.dravelo.example/

Our logo is attached to the brief.

Target Market(s)

Our target market is female, age 20-50. However should not alienate the design conscious male customer therefore

Industry/Entity Type

E-Commerce

Requirements
Must have
• - A featured product banner which includes a photograph and text. This should be easy to edit as we will be changing the featured product regularly
- An easily expendable products section with categories. Examples of categories could be cushions, bedding, crockery etc. Should be easy to add new categories as well as new product pictures
- Home/landing page should be uncluttered
- Should use the logo and should be easy to change the logo which we have in various colour combinations. We plan to change the logo colours depending on circumstance e.g. make it red and white around Valentines day (similar to the way Vintrel frequently changes the logo on their landing page)

```html
<!DOCTYPE html>
<html lang="en">
<head>
<meta charset="utf-8">
<title>Lindiwe Home – Homeware &amp; Accessories</title>
<link href="https://fonts.googleapis.com/css2?family=Open+Sans:wght@400;600;700;800&display=swap" rel="stylesheet">
<style>
:root{
  --teal:#1a9e9c;
  --teal-soft:#49b5b2;
  --orange:#d94a12;
  --yellow:#f7f38f;
  --page:#f9f9f9;
  --panel:#efefef;
  --band:#e2e2e2;
  --ink:#555;
  --white:#fff;
}
*{box-sizing:border-box;margin:0;padding:0}
html,body{width:772px;height:1200px;overflow:hidden}
body{position:relative;background:var(--page);font-family:"Open Sans",sans-serif;color:var(--ink)}
.abs{position:absolute}

/* header */
.account-bar{left:442px;top:-1px;width:248px;height:21px;background:var(--teal);border-radius:11px;display:flex;justify-content:center;align-items:center;gap:6px;color:var(--white);font-size:9px;font-weight:600}
.account-bar .sep{opacity:.8}
.search{left:566px;top:34px;width:124px;height:14px;border:1px solid #bbb;background:var(--white);font-size:8px;line-height:11px;color:#999;padding:0 8px}
.search svg{position:absolute;right:4px;top:1px}
.call{left:592px;top:68px;display:flex;gap:6px;align-items:center}
.call .label{color:var(--teal);font-size:11px;line-height:12px}
.call .number{color:var(--orange);font-size:11.5px;font-weight:700;line-height:13px}
.brand{left:78px;top:56px;width:92px;text-align:center}
.brand .name{display:flex;align-items:center;justify-content:center;gap:5px;color:var(--orange);font-size:11px;font-weight:600;letter-spacing:1px;line-height:14px;white-space:nowrap}
.brand .dot{width:9px;height:9px;border-radius:50%;background:var(--orange);flex:none}
.brand .tag{color:var(--teal);font-size:5px;margin-top:2px}
.main-nav{left:81px;top:118px;width:610px;display:flex;justify-content:space-between;font-size:9.5px;color:var(--ink)}
.main-nav .current{color:var(--orange);font-weight:700}
.main-nav .arrow{font-size:8px}
.rule-dashed{left:4px;top:139px;width:766px;border-top:1px dashed #888}

/* hero */
.hero{left:78px;top:157px;width:612px;height:233px;background:var(--teal)}
.hero-photo{left:15px;top:13px;width:380px;height:207px;background:linear-gradient(150deg,#efece5 0%,#e3d7c2 45%,#b98f67 80%,#9a6e4a 100%)}
.hero-copy{left:417px;top:33px;width:171px;height:156px;background:var(--teal-soft);color:var(--white);text-align:center;font-size:10.5px;font-weight:700;line-height:14.2px;padding-top:27px}
.order-btn{display:block;margin:25px auto 0;width:97px;height:19px;background:var(--orange);color:var(--white);font-size:10.5px;font-weight:700;line-height:19px}
.dots{left:487px;top:204px;display:flex;gap:4px}
.dots i{width:6px;height:6px;border-radius:50%;background:#ddd;display:block}
.dots i.on{background:var(--white);box-shadow:0 0 0 1.5px var(--orange) inset}

/* promo cards */
.promo{top:405px;width:291px;height:115px;border:7px solid var(--orange);background:var(--yellow)}
.promo h2{position:absolute;color:var(--teal);font-weight:800;font-size:25px;line-height:27px}
.promo-story{left:80px}
.promo-story h2{left:23px;top:37px}
.promo-story .portrait{left:187px;top:1px;width:88px;height:100px;background:linear-gradient(180deg,#7a7c80,#a99585 60%,#5a5556)}
.promo-design{left:400px}
.promo-design h2{left:22px;top:10px}
.promo-design .plate{left:151px;top:8px;width:118px;height:84px;background:linear-gradient(135deg,#c99a76,#9c6a47)}

/* products */
.shop{left:78px;top:547px;width:612px;height:360px;background:var(--panel)}
.shop-head{position:absolute;top:0;height:27px;font-size:9.5px;font-weight:700;color:var(--orange);text-align:center;line-height:27px}
.shop-head.cats{left:0;width:131px}
.shop-head.feat{left:131px;width:481px;background:var(--page);border-bottom:1px solid #e6e6e6}
.sidebar{left:0;top:27px;width:131px;height:333px;border-right:1px dashed #ddd}
.cat{position:absolute;left:1px;width:128px;height:24px;color:var(--white);font-size:10px;font-weight:700;line-height:24px;padding-left:38px}
.cat .toggle{position:absolute;right:10px;top:8px;width:9px;height:9px;font-size:9px;line-height:8px;text-align:center}
.cat.open{background:var(--teal);top:1px}
.cat.open .toggle{background:var(--orange)}
.cat.closed{background:var(--orange)}
.cat.closed .toggle{background:var(--teal)}
.sub{position:absolute;left:40px;top:37px;font-size:8.5px;line-height:14.7px;list-style:none}
.product{position:absolute;width:140px;text-align:center}
.product .frame{width:82px;height:82px;margin:0 auto;transform:rotate(45deg);border:4px solid var(--orange);border-radius:5px;box-shadow:0 2px 3px rgba(0,0,0,.2)}
.product .title{margin-top:32px;font-size:9.5px;font-weight:700;color:var(--ink)}
.next{left:592px;top:161px;width:22px;height:60px;background:var(--white);border-radius:8px 0 0 8px}

/* footer */
.footer-rule{left:78px;top:934px;width:612px;border-top:1px solid #ccc}
.ftitle{position:absolute;color:var(--teal);font-size:14px;font-weight:400;top:943px}
.quick-links{left:118px;top:978px;list-style:none;font-size:9.5px;line-height:16px}
.vdivider{top:950px;height:158px;border-left:1px dashed #999}
.field{position:absolute;left:265px;width:183px;height:18px;background:var(--white);border:1px solid #ccc;border-radius:2px;font-size:7.5px;font-style:italic;color:#666;padding:3px 6px}
.submit{left:266px;top:1098px;width:44px;height:15px;background:var(--orange);color:var(--white);font-size:9px;font-weight:700;text-align:center;line-height:15px}
.newsletter{left:494px;top:976px;width:160px;height:27px;background:#999;padding:5px 6px}
.newsletter .input{width:122px;height:15px;background:var(--white);font-size:8px;color:#666;padding:1px 6px}
.newsletter .send{position:absolute;right:6px;top:7px;width:24px;height:12px;background:var(--white)}
.newsletter::after{content:"";position:absolute;left:20px;bottom:-6px;border:6px solid transparent;border-top-color:#999;border-bottom:0}
.news-hint{left:501px;top:1010px;font-size:9.5px}
.social{left:494px;top:1083px;display:flex;gap:5px}
.social i{display:block;width:21px;height:21px;border-radius:50%}
.pay-band{left:78px;top:1123px;width:612px;height:53px;background:var(--band);text-align:center}
.pay-band h3{color:var(--teal);font-weight:400;font-size:11px;margin-top:8px}
.cards{display:flex;gap:5px;justify-content:center;margin-top:6px}
.cards i{display:block;width:26px;height:18px;border-radius:2px}
.copyright{left:0;top:1182px;width:772px;text-align:center;font-size:8px;color:#555}
</style>
</head>
<body>

<header>
  <nav class="abs account-bar"><span>Login</span><span class="sep">|</span><span>Sign Up</span><span class="sep">|</span><span>My Account</span><span class="sep">|</span><span>Shopping Cart</span></nav>
  <div class="abs search">Search
    <svg width="10" height="10" viewBox="0 0 10 10"><circle cx="4" cy="4" r="3" fill="none" stroke="#999" stroke-width="1.3"/><line x1="6.2" y1="6.2" x2="9.2" y2="9.2" stroke="#999" stroke-width="1.5"/></svg>
  </div>
  <div class="abs call">
    <svg width="10" height="20" viewBox="0 0 10 20"><path d="M8 1 C2 2 1 6 1 10 C1 14 2 18 8 19 L9 16 C5 15 5 12 5 10 C5 8 5 5 9 4 Z" fill="#222"/></svg>
    <div><div class="label">Call us</div><div class="number">123-456-7890</div></div>
  </div>
  <div class="abs brand">
    <div class="name"><span class="dot"></span>LINDIWE HOME</div>
    <div class="tag">homeware &amp; accessories</div>
  </div>
  <nav class="abs main-nav">
    <span class="current">Shop Now</span><span class="arrow">&gt;</span><span>Our Story</span><span class="arrow">&gt;</span><span>Blog</span><span class="arrow">&gt;</span><span>Custom Design</span><span class="arrow">&gt;</span><span>Our Shop</span><span class="arrow">&gt;</span><span>Press &amp; Mentions</span><span class="arrow">&gt;</span><span>Designer &amp; Architects</span><span class="arrow">&gt;</span><span>Video</span><span class="arrow">&gt;</span><span>Contact</span>
  </nav>
  <div class="abs rule-dashed"></div>
</header>

<section class="abs hero">
  <div class="abs hero-photo" role="img" aria-label="Featured product photo: yellow chair with a patterned cushion, small figurines, a carved mask and hand-painted wooden bowls"></div>
  <div class="abs hero-copy">
    Lorem ipsum lorelorem<br>loremipsuim lorem<br>lorem ipsum loremlorem<br>loremipsuim lorem<br>lorem ipsum loremlorem
    <span class="order-btn">ORDER NOW</span>
  </div>
  <div class="abs dots"><i></i><i></i><i class="on"></i><i></i></div>
</section>

<a class="abs promo promo-story">
  <h2>Our Story</h2>
  <div class="abs portrait" role="img" aria-label="Portrait of the founder wearing a headwrap"></div>
</a>
<a class="abs promo promo-design">
  <h2>Designer<br>&amp;<br>Architects</h2>
  <div class="abs plate" role="img" aria-label="Hand-painted terracotta plate"></div>
</a>

<section class="abs shop">
  <div class="shop-head cats">CATEGORIES</div>
  <div class="shop-head feat">FEATURED PRODUCTS</div>
  <aside class="abs sidebar">
    <div class="cat open">Cushions<span class="toggle">-</span></div>
    <ul class="sub"><li>Lorem ipsum</li><li>Lorem ipsum</li><li>Lorem ipsum</li><li>Lorem ipsum</li></ul>
    <div class="cat closed" style="top:100px">Bedding<span class="toggle">+</span></div>
    <div class="cat closed" style="top:135px">Crockery<span class="toggle">+</span></div>
  </aside>

  <div class="product" style="left:165px;top:59px"><div class="frame" role="img" aria-label="Beaded wire sculpture" style="background:linear-gradient(135deg,#3a3a3a,#9a9a9a 60%,#b86a4c)"></div><div class="title">LOREM IPSUM</div></div>
  <div class="product" style="left:302px;top:59px"><div class="frame" role="img" aria-label="Red and cream woven fans" style="background:linear-gradient(135deg,#9c2020,#d8cfbd)"></div><div class="title">LOREM IPSUM</div></div>
  <div class="product" style="left:439px;top:59px"><div class="frame" role="img" aria-label="Beaded wire lizards" style="background:linear-gradient(135deg,#cfcfcf,#a39a78 55%,#c57f7a)"></div><div class="title">LOREM IPSUM</div></div>
  <div class="product" style="left:165px;top:225px"><div class="frame" role="img" aria-label="White ceramic vases" style="background:linear-gradient(135deg,#8a8a8a,#e8e3d8)"></div><div class="title">LOREM IPSUM</div></div>
  <div class="product" style="left:302px;top:225px"><div class="frame" role="img" aria-label="Woven grass baskets" style="background:linear-gradient(135deg,#4a4a4a,#c9a66e)"></div><div class="title">LOREM IPSUM</div></div>
  <div class="product" style="left:439px;top:225px"><div class="frame" role="img" aria-label="Woven basket in yellow, grey and white" style="background:linear-gradient(135deg,#d9cc5a,#9a9a9a 60%,#e4e4e4)"></div><div class="title">LOREM IPSUM</div></div>

  <div class="abs next"><svg width="22" height="60" viewBox="0 0 22 60"><polyline points="8,22 14,30 8,38" fill="none" stroke="#bbb" stroke-width="2"/></svg></div>
</section>

<footer>
  <div class="abs footer-rule"></div>
  <h3 class="ftitle" style="left:117px">Quick Links</h3>
  <ul class="abs quick-links"><li>Shop Now</li><li>Our Story</li><li>Blog</li><li>Custom Design</li><li>Our Shop</li><li>Press &amp; Mentions</li><li>Designer &amp; Architects</li><li>Video</li><li>Contact</li></ul>
  <div class="abs vdivider" style="left:244px"></div>

  <h3 class="ftitle" style="left:266px">QUICK CONTACT</h3>
  <div class="field" style="top:976px">Name</div>
  <div class="field" style="top:998px">Phone</div>
  <div class="field" style="top:1020px">Email</div>
  <div class="field" style="top:1042px;height:46px">Message</div>
  <div class="abs submit">Submit</div>
  <div class="abs vdivider" style="left:470px"></div>

  <h3 class="ftitle" style="left:492px">NEWSLETTER</h3>
  <div class="abs newsletter"><div class="input">your email...</div><span class="send"></span></div>
  <div class="abs news-hint">Leave your email to subscribe</div>
  <h3 class="ftitle" style="left:492px;top:1049px">FOLLOW US ON</h3>
  <div class="abs social">
    <i style="background:#4ab3e0"></i><i style="background:#2b5aa6"></i><i style="background:#333"></i><i style="background:#f08a24"></i><i style="background:#d92332"></i><i style="background:#b8323c"></i>
  </div>

  <div class="abs pay-band">
    <h3>SECURE PAYMENT</h3>
    <div class="cards"><i style="background:#d8462a"></i><i style="background:#2b61b8"></i><i style="background:#1d5aa8"></i><i style="background:#1e4d94"></i><i style="background:#4d8bd4"></i><i style="background:#f5f5f5;border:1px solid #bbb"></i></div>
  </div>
  <div class="abs copyright">© 2014. LindiweHome. All Rights Reserved.</div>
</footer>

</body>
</html>
```